Business Card Design Project

We are a construction company in Orange County, CA. We need a two sided business card. We would like the back to be our logo with web URL. Front should included Name, title, address, phone, fax and email address.

our address is
627 West Dorrance Blvd, Suite 308
Anaheim, CA 92718

Our logo files are attached.

Construction

```html
<!DOCTYPE html>
<html lang="en">
<head>
<meta charset="utf-8">
<title>VERAX Business Card — Front and Back</title>
<link rel="stylesheet" href="https://fonts.googleapis.com/css2?family=Source+Sans+3:wght@400;700&display=swap">
<style>
  :root {
    --brand-blue: #1a4a80;
    --ink: #3a3a3a;
    --muted: #555555;
    --rule: #9a9a9a;
    --rule-dark: #333333;
    --paper: #ffffff;
    --backdrop: #ececec;
    --edge: #c8c8c8;
  }
  * { box-sizing: border-box; margin: 0; padding: 0; }
  html, body {
    width: 1200px; height: 1082px; overflow: hidden;
    background: var(--backdrop);
    font-family: "Source Sans 3", "Myriad Pro", sans-serif;
  }
  .canvas { position: relative; width: 1200px; height: 1082px; }

  .card {
    position: absolute; width: 764px; height: 437px;
    background: var(--paper); border: 1px solid var(--edge); overflow: hidden;
  }
  .card--front { left: 89px; top: 70px; }
  .card--back  { left: 357px; top: 545px; }

  .company-name {
    position: absolute; left: 0; width: 100%; text-align: center;
    color: var(--brand-blue); font-weight: 700;
    font-size: 104px; line-height: 1; letter-spacing: 1px;
  }
  .card--front .company-name { top: 60px; }
  .card--back  .company-name { top: 122px; }

  .address {
    position: absolute; right: 404px; top: 245px; text-align: right;
    font-style: normal; font-size: 18px; line-height: 25px; color: var(--ink);
  }
  .divider {
    position: absolute; left: 386px; top: 233px; width: 1px; height: 105px;
    background: var(--rule);
  }
  .contact {
    position: absolute; left: 419px; top: 231px; list-style: none;
    font-size: 18px; line-height: 24.5px; color: var(--ink);
  }
  .contact li { display: flex; align-items: center; gap: 7px; }
  .contact svg { width: 13px; height: 13px; fill: var(--ink); flex: none; }

  .rule-thin {
    position: absolute; left: 0; top: 377px; width: 100%; height: 2px;
    background: var(--rule-dark);
  }
  .name-band {
    position: absolute; left: 0; top: 385px; width: 100%; height: 52px;
    background: var(--brand-blue); color: #fff;
    display: flex; align-items: center; justify-content: center;
    font-size: 27px;
  }
  .name-band strong { font-weight: 700; margin-right: 6px; }

  .web-url {
    position: absolute; left: 0; top: 280px; width: 100%; text-align: center;
    font-size: 20px; letter-spacing: 3.5px; color: var(--muted);
  }
</style>
</head>
<body>
<main class="canvas">

  <section class="card card--front" aria-label="Card front">
    <p class="company-name">VERAX</p>

    <address class="address">
      627 West Dorrance Blvd<br>
      Suite 308, Anaheim<br>
      CA&nbsp; 92718
    </address>

    <div class="divider"></div>

    <ul class="contact">
      <li>
        <svg viewBox="0 0 16 16" aria-label="Phone"><path d="M3.5 1l3 3-1.6 2a9 9 0 0 0 5.1 5.1l2-1.6 3 3-2 2C7 14.5 1.5 9 1.5 3z"/></svg>
        01-555-0142
      </li>
      <li>
        <svg viewBox="0 0 16 16" aria-label="Fax"><path d="M4 1h8v4H4zM1 6h14v6h-3v3H4v-3H1zM5 10v4h6v-4z"/></svg>
        01-555-0143
      </li>
      <li>
        <svg viewBox="0 0 16 16" aria-label="Email"><path d="M1 3h14v10H1zM2 4l6 5 6-5z"/></svg>
        info@veraxbuild.com
      </li>
      <li>
        <svg viewBox="0 0 16 16" aria-label="Website"><circle cx="8" cy="8" r="7"/><path d="M1 8h14M8 1v14" stroke="#fff" stroke-width="1" fill="none"/></svg>
        www.veraxbuild.com
      </li>
    </ul>

    <div class="rule-thin"></div>
    <div class="name-band"><strong>Your Name,</strong> Title</div>
  </section>

  <section class="card card--back" aria-label="Card back">
    <p class="company-name">VERAX</p>
    <p class="web-url">www.veraxbuild.com</p>
  </section>

</main>
</body>
</html>
```